Professional violinist needs business cards

I am trying to attract the following jobs:
-private violin lessons (primarily classical)
-performance gigs (weddings, birthday parties, funerals, etc.)
-collaborations with other artists (studio recordings, performances)

I want to communicate that I have a very high standard of excellence for my work, but I also love people and celebrations.
Values/style words I like are:
love, joy, peace, fun, beauty, authenticity, excellence, warmth, refined/sleek, free spirited. If that's too confusing, just ignore :)

I will attach my favorite business card template that I could find on Canva. The lines are supposed to be like a music staff, which I think is really cool, but I also don't want it to look too busy. I like the simple black and white--I think it looks sharp--but I also am open to other ideas. I also have seen business cards with pictures included that looked great, so I attached an image that could be used as well.

I am also attaching a file that I made of my initials that could be used as a logo, but I'm not sure if it should be included.

Information on the card:
-My name (18 letters total)
-"violinist"
-phone number, email, website

Thank you!

```html
<!DOCTYPE html>
<html lang="en">
<head>
<meta charset="utf-8">
<title>Livia Harrowgate – Violinist Business Card</title>
<link href="https://fonts.googleapis.com/css2?family=Barlow+Condensed:wght@300;400;600&display=swap" rel="stylesheet">
<style>
  :root {
    --backdrop: #4b4d51;
    --card-black: #050506;
    --ink-white: #ffffff;
    --photo-light: #e6e6e7;
    --photo-mid: #c4c4c6;
    --photo-dark: #8d8d90;
    --emblem-ring: #1a1a1c;
    --emblem-text: #111113;
  }
  * { margin: 0; padding: 0; box-sizing: border-box; }
  html, body {
    width: 1200px;
    height: 1200px;
    overflow: hidden;
    background: var(--backdrop);
    font-family: "Barlow Condensed", "Arial Narrow", sans-serif;
  }
  .canvas {
    position: relative;
    width: 1200px;
    height: 1200px;
  }
  .card {
    position: absolute;
    left: 220px;
    width: 760px;
    height: 434px;
    overflow: hidden;
    box-shadow: 0 14px 30px rgba(0,0,0,0.35);
  }
  .card-front { top: 120px; }
  .card-back { top: 614px; background: var(--card-black); }

  .front-photo {
    position: absolute;
    inset: 0;
    background:
      radial-gradient(ellipse 22% 32% at 78% 62%, var(--photo-dark) 0%, rgba(141,141,144,0) 100%),
      radial-gradient(ellipse 30% 40% at 12% 70%, var(--photo-mid) 0%, rgba(196,196,198,0) 100%),
      linear-gradient(160deg, var(--photo-light) 0%, #d6d6d8 45%, var(--photo-mid) 100%);
  }
  .front-emblem {
    position: absolute;
    left: 175px;
    top: 118px;
    width: 230px;
    height: 190px;
    border-radius: 50%;
    background: var(--ink-white);
    border: 8px solid var(--emblem-ring);
    display: flex;
    align-items: center;
    justify-content: center;
  }
  .emblem-name {
    font-weight: 600;
    font-size: 22px;
    letter-spacing: 1px;
    color: var(--emblem-text);
    text-transform: uppercase;
  }

  .back-details {
    position: absolute;
    left: 300px;
    top: 92px;
    color: var(--ink-white);
  }
  .artist-name {
    font-size: 46px;
    line-height: 1;
    text-transform: uppercase;
    letter-spacing: 0.5px;
  }
  .artist-name .first { font-weight: 600; }
  .artist-name .last { font-weight: 400; }
  .artist-role {
    margin-top: 12px;
    font-weight: 300;
    font-size: 24px;
    letter-spacing: 10px;
    text-transform: uppercase;
  }
  .contact-list {
    list-style: none;
    margin-top: 34px;
  }
  .contact-list li {
    font-weight: 400;
    font-size: 30px;
    line-height: 1;
    margin-bottom: 22px;
  }
</style>
</head>
<body>
  <main class="canvas">
    <section class="card card-front">
      <div class="front-photo" role="img" aria-label="Soft-focus black and white photograph of leaves and branches"></div>
      <div class="front-emblem">
        <span class="emblem-name">Livia Harrowgate</span>
      </div>
    </section>

    <section class="card card-back">
      <div class="back-details">
        <h1 class="artist-name"><span class="first">Livia</span> <span class="last">Harrowgate</span></h1>
        <p class="artist-role">Violinist</p>
        <ul class="contact-list">
          <li class="contact-phone">+00 4821 360 775</li>
          <li class="contact-email">liviaharrowgate@mailbox.com</li>
          <li class="contact-web">www.liviaharrowgate.com</li>
        </ul>
      </div>
    </section>
  </main>
</body>
</html>
```